Custom unique Stationary design for Logistics company

We need a custom, unique , elegant and luxurious full stationary design using our new logo, following these guidelines:
1- Business card: double sided, both sides uses the navy blue as the background main color (same as the code of the navy blue used in our logo).
2- envelope and folder: also use the same navy blue as the main background color.
3- book cover( notepad cover) : same thing with the navy blue
4- letterhead: feel free to use the combination of the colors in our logo.
5- rest of the items are up to your creativity

Target Market(s)

corporates and other businesses

Industry/Entity Type

Logistics and heavy machines contractors

Requirements
Must have
• Letterhead, business card, envelope, notepad cover, paper, file
Nice to have
• navy blue to be main background color for business card, envelope, notepad cover

```html
<!DOCTYPE html>
<html lang="en">
<head>
<meta charset="utf-8">
<title>Northway Freight Company – Business Card</title>
<link rel="stylesheet" href="https://fonts.googleapis.com/css2?family=Arimo:wght@400;700&display=swap">
<style>
  :root {
    --backdrop: #2b2c2e;
    --navy: #02527a;
    --navy-emboss: #0b6396;
    --orange: #f25c2a;
    --white: #ffffff;
    --silver: #b9c3cc;
  }
  * { box-sizing: border-box; margin: 0; padding: 0; }
  html, body { width: 1200px; height: 1015px; overflow: hidden; }
  body {
    background: var(--backdrop);
    font-family: "Arimo", Arial, sans-serif;
    display: flex;
    flex-direction: column;
    align-items: center;
    justify-content: center;
    gap: 44px;
  }
  .card {
    position: relative;
    width: 760px;
    height: 434px;
    background: var(--navy);
    overflow: hidden;
  }

  /* Front */
  .card-front {
    display: flex;
    align-items: center;
    justify-content: center;
    gap: 22px;
  }
  .brand-dot {
    width: 34px;
    height: 34px;
    border-radius: 50%;
    background: var(--orange);
  }
  .brand-name {
    color: var(--white);
    font-weight: 700;
    font-size: 44px;
    letter-spacing: 1px;
    text-transform: uppercase;
  }

  /* Back */
  .chevron {
    position: absolute;
    left: 0;
    top: 104px;
    width: 52px;
    height: 64px;
  }
  .details {
    position: absolute;
    left: 96px;
    top: 96px;
    color: var(--white);
  }
  .person-name {
    color: var(--orange);
    font-size: 27px;
    font-weight: 400;
    text-transform: uppercase;
    line-height: 1;
  }
  .person-role {
    font-size: 17px;
    text-transform: uppercase;
    margin-top: 6px;
    letter-spacing: 0.3px;
  }
  .contact-list {
    list-style: none;
    margin-top: 34px;
    font-size: 19px;
    line-height: 30px;
  }
  .contact-list li { display: flex; align-items: center; gap: 10px; }
  .contact-icon { width: 18px; height: 18px; flex: none; }
  .address {
    margin-top: 44px;
    font-size: 19px;
    line-height: 26px;
    font-style: normal;
  }
  .emboss-name {
    position: absolute;
    right: 40px;
    top: 58px;
    color: var(--navy-emboss);
    font-weight: 700;
    font-size: 62px;
    text-transform: uppercase;
    letter-spacing: 1px;
  }
</style>
</head>
<body>

  <section class="card card-front" aria-label="Business card front">
    <span class="brand-dot"></span>
    <span class="brand-name">Northway Freight Company</span>
  </section>

  <section class="card card-back" aria-label="Business card back">
    <span class="emboss-name">Northway</span>

    <svg class="chevron" viewBox="0 0 52 64" aria-hidden="true">
      <polygon points="0,0 26,0 52,32 26,64 0,64 22,32" fill="var(--orange)"/>
    </svg>

    <div class="details">
      <h1 class="person-name">Daniel Carver</h1>
      <p class="person-role">Managing Director</p>

      <ul class="contact-list">
        <li>
          <svg class="contact-icon" viewBox="0 0 24 24" aria-hidden="true">
            <path d="M6.6 10.8c1.4 2.8 3.8 5.1 6.6 6.6l2.2-2.2c.3-.3.7-.4 1-.2 1.1.4 2.3.6 3.6.6.6 0 1 .4 1 1V20c0 .6-.4 1-1 1C10.6 21 3 13.4 3 4c0-.6.4-1 1-1h3.5c.6 0 1 .4 1 1 0 1.3.2 2.5.6 3.6.1.3 0 .7-.2 1l-2.3 2.2z" fill="var(--orange)"/>
          </svg>
          021-555 018 342
        </li>
        <li>
          <svg class="contact-icon" viewBox="0 0 24 24" aria-hidden="true">
            <rect x="2" y="5" width="20" height="14" fill="var(--orange)"/>
            <polyline points="2,5 12,13 22,5" fill="none" stroke="var(--navy)" stroke-width="2"/>
          </svg>
          hello@northwayfreight.com
        </li>
        <li>
          <svg class="contact-icon" viewBox="0 0 24 24" aria-hidden="true">
            <circle cx="12" cy="12" r="10" fill="var(--orange)"/>
            <g fill="none" stroke="var(--navy)" stroke-width="1.5">
              <ellipse cx="12" cy="12" rx="4" ry="10"/>
              <line x1="2" y1="12" x2="22" y2="12"/>
              <line x1="4" y1="7" x2="20" y2="7"/>
              <line x1="4" y1="17" x2="20" y2="17"/>
            </g>
          </svg>
          www.northwayfreight.com
        </li>
      </ul>

      <address class="address">
        87, Harbour Gate Road<br>
        30918, Eastland
      </address>
    </div>
  </section>

</body>
</html>
```